Norrell Advisory WA Business Card

Create an interesting, eye catching and colourful two sided business card. We are a business consulting operation assisting SME's improve all areas of their business. We provide consulting services to assist SME's to create a culture of continuous improvement, making a positive difference in the business. Our tag line is Small changes, big rewards. We want to create a well recognised, innovative brand that can be continued throughout our website, social media and email correspondence.

Target Market(s)

Small to Medium Enterprise Business Owners

Industry/Entity Type

Business Consultant

Contact Information for Business Card

Name of Business: Norrell Advisory - Steady Steps Lasting Gains
Derek Holloway Ph 0407385510 Megan Holloway Ph 0407913847
Email norrelladvisorywa@mailbox-example.com
Web address TBA
FaceBook page TBA

BACKSIDE OF CARD

Providing assistance with:

• Organisation & Efficiency
• Revenue generation & Marketing
• Financial Management
• Production quality & delivery
• Systems & Process documentation
• Exit Strategy

Font styles to use
Other font styles liked:
• Calibri

Colors

Designer to choose colors to be used in the design.

Requirements
Must have
• Calibri font

```html
<!DOCTYPE html>
<html lang="en">
<head>
<meta charset="utf-8">
<title>Norrell Advisory WA – Business Card</title>
<link rel="stylesheet" href="https://fonts.googleapis.com/css2?family=Open+Sans:wght@400;600;700&family=Carlito:wght@400;700&display=swap">
<style>
  :root {
    --page-bg: #e6e6e6;
    --card-white: #ffffff;
    --card-dark: #2e2d2d;
    --ink: #333333;
    --ink-soft: #3d3d3d;
    --brand-blue: #0e78bd;
    --accent-blue: #2a8fd0;
    --sky: #4aa8d8;
    --white: #ffffff;
  }
  * { box-sizing: border-box; margin: 0; padding: 0; }
  html, body {
    width: 1125px; height: 1200px; overflow: hidden;
    background: var(--page-bg);
  }
  .sheet { position: relative; width: 1125px; height: 1200px; }

  .card {
    position: absolute;
    left: 157px;
    width: 826px;
    height: 472px;
    overflow: hidden;
  }
  .card--front { top: 106px; background: var(--card-white); }
  .card--back { top: 640px; background: var(--card-dark); }

  /* Front */
  .front-artwork {
    position: absolute; left: 0; top: 0;
    width: 405px; height: 472px;
    background: linear-gradient(150deg, #1480c2 0%, #5fb7e0 28%, #fdc52f 45%, #ef4536 62%, #8cc341 100%);
  }

  .company {
    position: absolute; left: 455px; top: 72px;
    font-family: "Open Sans", sans-serif;
  }
  .company__name {
    font-weight: 700; font-size: 30px; line-height: 1;
    color: var(--ink); letter-spacing: 0.2px;
  }
  .company__tagline {
    margin-top: 8px;
    font-weight: 400; font-size: 17px; line-height: 1;
    color: var(--ink-soft); letter-spacing: 2px;
  }

  .contacts {
    position: absolute; left: 455px; top: 188px;
    font-family: "Open Sans", sans-serif;
  }
  .person { margin-bottom: 12px; }
  .person__name {
    font-weight: 700; font-size: 29px; line-height: 1.05;
    color: var(--brand-blue);
  }
  .person__phone {
    font-weight: 700; font-size: 18px; line-height: 1.3;
    color: var(--ink-soft);
  }
  .details {
    position: absolute; left: 455px; top: 326px;
    font-family: "Open Sans", sans-serif;
    font-size: 17.5px; line-height: 25px; color: var(--ink-soft);
    list-style: none;
  }
  .details__social { display: flex; align-items: center; gap: 9px; }
  .details__social-mark {
    width: 16px; height: 16px; background: var(--ink-soft); display: inline-block;
  }

  /* Back */
  .brand-block {
    position: absolute; left: 75px; top: 142px; width: 272px;
    text-align: center; font-family: "Open Sans", sans-serif; color: var(--white);
  }
  .brand-block__mark {
    display: block; width: 110px; height: 110px; margin: 0 auto 26px;
    background: var(--accent-blue);
  }
  .brand-block__name {
    font-weight: 700; font-size: 26px; line-height: 1; letter-spacing: 0.2px;
  }
  .brand-block__tagline {
    margin-top: 6px; font-size: 14.5px; line-height: 1; letter-spacing: 1.6px;
  }

  .services {
    position: absolute; left: 399px; top: 130px;
    font-family: "Carlito", "Open Sans", sans-serif; color: var(--white);
  }
  .services__heading {
    font-family: "Open Sans", sans-serif;
    font-weight: 700; font-size: 25px; line-height: 1;
    color: var(--brand-blue); margin-bottom: 18px;
  }
  .services__list { list-style: none; }
  .services__item {
    display: flex; align-items: center; gap: 9px;
    font-size: 21px; line-height: 26px;
  }
  .services__bullet {
    width: 13px; height: 13px; background: var(--sky); flex: none;
  }
</style>
</head>
<body>
<main class="sheet">

  <section class="card card--front" aria-label="Business card front">
    <div class="front-artwork" role="img" aria-label="Large colourful brand artwork in blue, yellow, red and green"></div>

    <header class="company">
      <h1 class="company__name">NORRELL ADVISORY</h1>
      <p class="company__tagline">STEADY STEPS LASTING GAINS</p>
    </header>

    <div class="contacts">
      <div class="person">
        <p class="person__name">DEREK HOLLOWAY</p>
        <p class="person__phone">0407385510</p>
      </div>
      <div class="person">
        <p class="person__name">MEGAN HOLLOWAY</p>
        <p class="person__phone">0407913847</p>
      </div>
    </div>

    <ul class="details">
      <li>norrelladvisorywa@mailbox-example.com</li>
      <li>www.norrelladvisorywa.com</li>
      <li class="details__social"><span class="details__social-mark" aria-hidden="true"></span>/norrelladvisorywa</li>
    </ul>
  </section>

  <section class="card card--back" aria-label="Business card back">
    <div class="brand-block">
      <span class="brand-block__mark" aria-hidden="true"></span>
      <p class="brand-block__name">NORRELL ADVISORY</p>
      <p class="brand-block__tagline">STEADY STEPS LASTING GAINS</p>
    </div>

    <div class="services">
      <h2 class="services__heading">Providing assistance with</h2>
      <ul class="services__list">
        <li class="services__item"><span class="services__bullet" aria-hidden="true"></span>Organisation &amp; Efficiency</li>
        <li class="services__item"><span class="services__bullet" aria-hidden="true"></span>Revenue generation &amp; Marketing</li>
        <li class="services__item"><span class="services__bullet" aria-hidden="true"></span>Financial Management</li>
        <li class="services__item"><span class="services__bullet" aria-hidden="true"></span>Production quality &amp; delivery</li>
        <li class="services__item"><span class="services__bullet" aria-hidden="true"></span>Systems &amp; Process documentation</li>
        <li class="services__item"><span class="services__bullet" aria-hidden="true"></span>Exit Strategy</li>
      </ul>
    </div>
  </section>

</main>
</body>
</html>
```